Business Card Design Project

We are looking to redesign the logo, business card and stationary of one of our group companies - SOLARO SUPPLY HOUSE LLC.

The company specialises in industrial PVC and CPVC Piping systems. It is situated in the Middle East and the focus is purely in this region.

The logo work is already completed. The file is uploaded for the reference.

We are looking for a clean minimalistic design for the business card.

regards
Rohit
Updates

Hello Everyone!

Thanks for submitting your designs. 

Yet to find the right design. Probably the below links will give you guys some more idea on what we would like.

Minimalist design with some creativity.

Rohit

http://exampledesignfolio.com/inspiration/15-beautifully-minimal-business-cards

http://www.samplelayoutbase.com/2011/11/14/30-minimalist-business-card-design/

http://www.primepixelcraft.com/inspiration/minimal-business-cards/

Target Market(s)

Industrial users

Industry/Entity Type

Industrial

Requirements
Must have
• - Minimalistic design

- Back side of the card should include the manufacturer PIPEMARQ NORTHERN's decal. The file is upload for the reference

- Further information
Company Name:
SOLARO SUPPLY HOUSE LLC
Address:
PO Box 8152, Sharjah Industrial Area 4, Qarwan Road
Sharjah, United Arab Emirates
Telephone:
+971-6-5000-118
Fax:
+977-6-5000-119
Email:
mail@sshlexample.com

- FYI, Solaro Supply House LLC is the authorised distributor for PIPEMARQ NORTHERN in the UAE. For further information on pipemarq please visit the website www.pipemarq-example.ca

```html
<!DOCTYPE html>
<html lang="en">
<head>
<meta charset="utf-8">
<title>Solaro Supply House LLC – Business Card</title>
<link rel="stylesheet" href="https://fonts.googleapis.com/css2?family=Mulish:wght@400;700&display=swap">
<style>
  :root {
    --backdrop: #a3c8e4;
    --card-light: #ffffff;
    --card-light-edge: #e8eaea;
    --card-dark: #4a4a4a;
    --card-dark-edge: #2c2c2c;
    --brand-blue: #5277c4;
    --brand-grey: #9a9a9a;
    --text-white: #ffffff;
    --text-soft: #e6e6e6;
  }
  * { box-sizing: border-box; margin: 0; padding: 0; }
  html, body { width: 1200px; height: 960px; overflow: hidden; }
  body {
    background: var(--backdrop);
    font-family: "Mulish", sans-serif;
    position: relative;
  }
  .card {
    position: absolute;
    top: 319px;
    width: 450px;
    height: 243px;
    border-radius: 18px;
    overflow: hidden;
  }
  .card--front {
    left: 106px;
    background: radial-gradient(ellipse at 50% 45%, var(--card-light) 20%, var(--card-light-edge) 100%);
  }
  .card--back {
    left: 645px;
    background: radial-gradient(ellipse at 45% 45%, var(--card-dark) 0%, var(--card-dark-edge) 100%);
    color: var(--text-white);
  }
  .edge-tab {
    position: absolute;
    top: 99px;
    width: 12px;
    height: 46px;
    background: var(--brand-blue);
  }
  .card--front .edge-tab { right: 0; }
  .card--back .edge-tab { left: 0; }

  .brand {
    position: absolute;
    left: 0; right: 0;
    top: 90px;
    display: flex;
    align-items: center;
    justify-content: center;
    gap: 12px;
  }
  .brand__square {
    width: 54px;
    height: 54px;
    border-radius: 12px;
    background: var(--brand-blue);
  }
  .brand__name {
    font-weight: 700;
    font-size: 17px;
    letter-spacing: 0.06em;
    color: var(--brand-grey);
    white-space: nowrap;
  }

  .back-square {
    position: absolute;
    right: -22px;
    top: 2px;
    width: 120px;
    height: 120px;
    border-radius: 26px;
    background: var(--brand-blue);
  }
  .person {
    position: absolute;
    left: 36px;
    top: 26px;
  }
  .person__name {
    font-weight: 700;
    font-size: 23px;
    line-height: 1.1;
  }
  .person__title {
    font-size: 17px;
    line-height: 1.1;
    color: var(--text-soft);
  }
  .contact {
    position: absolute;
    left: 36px;
    top: 98px;
    list-style: none;
    font-size: 13px;
    line-height: 16px;
    color: var(--text-soft);
  }
  .contact b { color: var(--text-white); font-weight: 700; }
  .address {
    position: absolute;
    left: 36px;
    bottom: 13px;
    font-size: 10px;
    color: var(--text-soft);
    white-space: nowrap;
  }
</style>
</head>
<body>
  <section class="card card--front" aria-label="Card front">
    <div class="brand">
      <span class="brand__square"></span>
      <span class="brand__name">SOLARO SUPPLY HOUSE LLC</span>
    </div>
    <span class="edge-tab"></span>
  </section>

  <section class="card card--back" aria-label="Card back">
    <span class="back-square"></span>
    <span class="edge-tab"></span>
    <div class="person">
      <p class="person__name">Your Name</p>
      <p class="person__title">Managing Director</p>
    </div>
    <ul class="contact">
      <li><b>T:</b> +971-6-5000-118</li>
      <li><b>F:</b> +977-6-5000-119</li>
      <li><b>E:</b> mail@sshlexample.com</li>
    </ul>
    <p class="address">PO Box 8152 &nbsp;|&nbsp; Industrial Area 4, Qarwan Road &nbsp;|&nbsp; Sharjah &nbsp;|&nbsp; United Arab Emirates</p>
  </section>
</body>
</html>
```